Business Cards for IT Consulting Company (Managed Service Provider)

I am looking to have some business cards printed and would like some designs. We are an IT Consulting company based in Vancouver BC. I would like a nice clean and modern look to the cards. I have uploaded all the versions of my logo so parts can be used as needed. Here is a snippit from our website homepage:

Quillbrook Networks Ltd. is an IT Solutions Partner located in Vancouver BC, Canada. We offer IT solutions and support to customers in the greater Vancouver Area. With expertise in Microsoft platforms, as well as Linux and Mac OSX and over 12 years experience in the IT industry, Quillbrook Networks is dedicated to offering our clients top quality service and products. We take pride in the solutions we offer our customers. The greatest compliment a client can give us is to recommend our services.

Quillbrook Networks Ltd. offers a wide range of IT services from onsite service to remote support and managed service solutions. This allows clients to choose the support path that best suits their company’s needs. Supporting many different sized companies from small to enterprise level over the past 12 years Quillbrook Networks has the experience and expertise needed to ensure things run smoothly. Allowing our clients to focus on doing business.

Revolutionizing the way IT services are delivered.

Quillbrook Networks is dedicated to providing our clients with IT solutions that work and grow with them for years to come. This philosophy helps save money in the long run instead of replacing equipment constantly. Far too often IT solutions are not well thought out and while possibly solving the problem at hand, require replacement due to growth or quality within a very short time frame. Quillbrook Networks takes pride in providing solutions that will last and be able to accommodate growth without the need for replacement.

Industry/Entity Type

Information Technology

Contact Information for Business Card

Quillbrook Networks Ltd.
(Employee Name)
Eml: (Employees Email Address)
Web: quillbrook.me
Ph: 604-555-0148

Font styles to use
Serif
Sans Serif

Requirements
Must have
• The Company logo and company colors.
Nice to have
• - Our tag line: "Revolutionizing IT Services" or "Revolutionizing the way IT services are delivered."
• - Also I really like the idea of nature and technology together blending which is sort of where my logo came from so integrating that somehow onto the business cards would be great.

```html
<!DOCTYPE html>
<html lang="en">
<head>
<meta charset="utf-8">
<title>Quillbrook Networks Ltd. – Business Card</title>
<link href="https://fonts.googleapis.com/css2?family=Montserrat:wght@400;500;600;700&display=swap" rel="stylesheet">
<style>
  :root {
    --page-bg: #e9e9e9;
    --card-grey: #6f6f70;
    --pattern-grey: #767677;
    --brand-blue: #00b1ec;
    --white: #ffffff;
    --shadow: rgba(0,0,0,0.18);
  }
  * { margin: 0; padding: 0; box-sizing: border-box; }
  html, body { width: 1200px; height: 1200px; overflow: hidden; }
  body {
    background: var(--page-bg);
    font-family: "Montserrat", Arial, sans-serif;
    position: relative;
  }
  .card {
    position: absolute;
    left: 200px;
    width: 800px;
    height: 457px;
    background: var(--card-grey);
    box-shadow: 0 10px 30px var(--shadow);
    overflow: hidden;
  }
  .card--front { top: 95px; }
  .card--back { top: 648px; }

  /* Front */
  .front-pattern {
    position: absolute; inset: 0;
    background: radial-gradient(circle at 40% 40%, var(--pattern-grey), var(--card-grey));
  }
  .front-brand {
    position: absolute;
    left: 110px; top: 245px;
    display: flex; align-items: center; gap: 22px;
  }
  .brand-square {
    width: 70px; height: 70px;
    background: var(--brand-blue);
    flex: none;
  }
  .brand-name {
    color: var(--brand-blue);
    font-weight: 700;
    font-size: 38px;
    line-height: 1.05;
  }
  .tagline {
    color: var(--white);
    font-size: 18px;
    font-weight: 500;
    margin-top: 8px;
  }

  /* Back */
  .back-panel {
    position: absolute; right: 0; top: 0;
    width: 300px; height: 100%;
    background: var(--brand-blue);
  }
  .back-brand {
    position: absolute; left: 50px; top: 42px;
    display: flex; align-items: center; gap: 14px;
  }
  .back-brand .brand-square { width: 44px; height: 44px; }
  .back-brand .brand-name { font-size: 26px; color: var(--white); }

  .person {
    position: absolute; left: 0; top: 165px; width: 500px;
  }
  .person-name {
    position: absolute; right: 40px; top: 0;
    color: var(--brand-blue);
    font-weight: 700; font-size: 25px; letter-spacing: 1.5px;
  }
  .person-rule { position: absolute; left: 0; top: 30px; }
  .person-title {
    position: absolute; right: 40px; top: 62px;
    color: var(--white);
    font-weight: 700; font-size: 15px; letter-spacing: 1px;
  }

  .contact-list {
    position: absolute; left: 38px; top: 262px;
    list-style: none;
  }
  .contact-item {
    display: flex; align-items: center; gap: 14px;
    color: var(--white);
    font-size: 17px;
    height: 30px;
  }
  .contact-icon {
    width: 20px; height: 20px;
    background: var(--brand-blue);
    border-radius: 3px;
    display: flex; align-items: center; justify-content: center;
    flex: none;
  }
</style>
</head>
<body>

  <section class="card card--front">
    <div class="front-pattern" role="img" aria-label="Subtle tonal pattern of outlined hexagons and cubes"></div>
    <div class="front-brand">
      <span class="brand-square"></span>
      <div>
        <div class="brand-name">Quillbrook<br>Networks Ltd.</div>
        <div class="tagline">Revolutionizing IT Services</div>
      </div>
    </div>
  </section>

  <section class="card card--back">
    <div class="back-panel" role="img" aria-label="Blue panel with faint large brand decoration"></div>

    <div class="back-brand">
      <span class="brand-square"></span>
      <span class="brand-name">Quillbrook Networks Ltd.</span>
    </div>

    <div class="person">
      <div class="person-name">DANA WHITLOCK</div>
      <svg class="person-rule" width="500" height="32" viewBox="0 0 500 32">
        <polyline points="0,20 105,20 125,8 250,8 270,28 460,28" fill="none" stroke="#00b1ec" stroke-width="2"/>
      </svg>
      <div class="person-title">DIRECTOR</div>
    </div>

    <ul class="contact-list">
      <li class="contact-item">
        <span class="contact-icon">
          <svg width="12" height="12" viewBox="0 0 24 24"><path d="M6 2l4 5-2 3c1 3 3 5 6 6l3-2 5 4-3 4C10 22 2 14 2 5z" fill="#6f6f70"/></svg>
        </span>604-555-0148
      </li>
      <li class="contact-item">
        <span class="contact-icon">
          <svg width="12" height="12" viewBox="0 0 24 24"><rect x="5" y="2" width="14" height="7" fill="#6f6f70"/><rect x="2" y="10" width="20" height="12" fill="#6f6f70"/></svg>
        </span>604-555-0192
      </li>
      <li class="contact-item">
        <span class="contact-icon">
          <svg width="12" height="12" viewBox="0 0 24 24"><circle cx="12" cy="12" r="9" fill="none" stroke="#6f6f70" stroke-width="3"/></svg>
        </span>danawhitlock
      </li>
      <li class="contact-item">
        <span class="contact-icon">
          <svg width="12" height="12" viewBox="0 0 24 24"><rect x="2" y="5" width="20" height="14" fill="none" stroke="#6f6f70" stroke-width="2.5"/><polyline points="2,5 12,13 22,5" fill="none" stroke="#6f6f70" stroke-width="2.5"/></svg>
        </span>danawhitlock@quillbrook.me
      </li>
      <li class="contact-item">
        <span class="contact-icon">
          <svg width="12" height="12" viewBox="0 0 24 24"><circle cx="12" cy="12" r="9" fill="none" stroke="#6f6f70" stroke-width="2"/><line x1="3" y1="12" x2="21" y2="12" stroke="#6f6f70" stroke-width="2"/><ellipse cx="12" cy="12" rx="4" ry="9" fill="none" stroke="#6f6f70" stroke-width="2"/></svg>
        </span>quillbrook.me
      </li>
    </ul>
  </section>

</body>
</html>
```